Brightline Energy Product Distribution Brochure

We are looking to have our current brochure for our customers completely redesigned...the idea is to present the relevant information in an attractive way . Our website is brightlineenergyco.example where you can find more information about us. We have included a file with a rough idea of the page order and what each should include but feel free to adapt based on design. The example provided is only for context and doesnt have to be maintained. We will be using the brochure both digitally and in print form. As long as it reads easily and is eye catching, the design can be horizontal or vertical.Final deliverable should be indesign file.

"Our Brands" page: should be limited to one page (space being enough) where it has the header for each one (for example diesel generators) space for one or two lines of text and then the corresponding logos for each of the five categories
Updates

For those asking: the "our brands" page should be a single page layout where there is a header with the corresponding section and space for maybe one line of text followed by the two logos for that category. Each of the product pages should be similar in fashion to the one in the document attached: a photo of the product with some white space and space for the text to be included. We will be posting additional examples today

Target Market(s)

We want to present it to customers both digitally and in print so they can see our products

Industry/Entity Type

Power Generation

Font styles to use
Serif

Requirements
Must have
• Eye catching and able to present the information in a presentable fashion. Rest is up to you.
Nice to have
• Should incorporate the colors of our logo but can also add other depending on design

```html
<!DOCTYPE html>
<html lang="en">
<head>
<meta charset="utf-8">
<title>Brightline Energy – Diesel Generators</title>
<link href="https://fonts.googleapis.com/css2?family=Montserrat:wght@300;400;600;800;900&display=swap" rel="stylesheet">
<style>
  :root {
    --navy: #0c1a3a;
    --navy-deep: #071129;
    --steel: #2b4a78;
    --yellow: #fdc010;
    --yellow-deep: #f2a900;
    --white: #ffffff;
    --ink: #1b1b1b;
    --grey-band: #4a4a4f;
    --canvas: #d3d4d6;
  }
  * { margin: 0; padding: 0; box-sizing: border-box; }
  html, body { width: 1200px; height: 801px; overflow: hidden; background: var(--canvas); }
  body { font-family: "Montserrat", Arial, sans-serif; }
  .spread { position: absolute; left: 0; top: 0; width: 1200px; height: 801px; display: flex; }
  .page { position: relative; width: 600px; height: 801px; overflow: hidden; }
  .page-backdrop {
    position: absolute; inset: 0;
    background:
      radial-gradient(ellipse at 45% 35%, rgba(90,130,190,.55), transparent 60%),
      radial-gradient(ellipse at 80% 85%, rgba(60,110,180,.6), transparent 55%),
      linear-gradient(160deg, var(--navy-deep) 0%, var(--navy) 45%, var(--steel) 100%);
  }
  .bands { position: absolute; inset: 0; width: 600px; height: 801px; }
  .eyebrow {
    position: absolute; left: 43px; top: 58px;
    color: var(--white); font-weight: 600; font-size: 26px; letter-spacing: .5px;
  }
  .eyebrow-rule { position: absolute; left: 43px; top: 97px; width: 56px; height: 4px; background: var(--yellow); }
  .headline {
    position: absolute; left: 42px; top: 104px;
    color: var(--yellow); font-weight: 900; font-size: 41px; letter-spacing: -.5px; white-space: nowrap;
  }
  .subhead {
    position: absolute; left: 43px; top: 174px;
    color: var(--white); font-weight: 600; font-size: 22px; line-height: 29px;
  }
  .product-photo {
    position: absolute; left: 230px; top: 173px; width: 323px; height: 210px;
    background: linear-gradient(180deg, #f4f4f4 0%, #e6e6e6 78%, #1c1c1c 80%, #2a2a2a 100%);
  }
  .features-label {
    position: absolute; left: 45px; top: 320px;
    color: var(--yellow); font-weight: 300; font-size: 16px;
  }
  .features-panel {
    position: absolute; left: 0; top: 357px; width: 405px; height: 334px;
    background: var(--white);
  }
  .feature-list {
    position: absolute; left: 42px; top: 24px; width: 290px;
    list-style: none; color: var(--ink); font-size: 10px; line-height: 13.4px;
  }
  .feature-list li { position: relative; padding-left: 19px; }
  .feature-list li::before {
    content: ""; position: absolute; left: 3px; top: 4px; width: 5px; height: 5px;
    border-radius: 50%; background: var(--yellow);
  }
  .site-photo { position: absolute; width: 135px; }
  .site-photo.upper { top: 449px; height: 141px; background: linear-gradient(135deg, #3a5a8a, #b86a2a 55%, #e8a040); }
  .site-photo.lower { top: 596px; height: 140px; background: linear-gradient(160deg, #dfe6ee, #7d99bd 55%, #d06a24); }
  .page-number {
    position: absolute; left: 20px; top: 756px; width: 70px; height: 40px;
    isolation: isolate; z-index: 2;
    color: var(--navy-deep); font-weight: 900; font-size: 26px; line-height: 40px; text-align: center;
  }
  .page-number::before {
    content: ""; position: absolute; inset: 0; z-index: -1;
    background: var(--yellow); transform: skewX(-28deg);
  }
  .page-number span { position: relative; }
</style>
</head>
<body>
<main class="spread">

  <section class="page page-left">
    <div class="page-backdrop" role="img" aria-label="Dark blue industrial plant at night with pipes and towers"></div>
    <svg class="bands" viewBox="0 0 600 801" aria-hidden="true">
      <polygon points="0,690 405,560 520,520 600,600 600,801 0,801" fill="var(--yellow)" opacity=".75"/>
      <polygon points="520,801 600,760 600,801" fill="var(--grey-band)"/>
      <polygon points="400,801 600,640 600,700 470,801" fill="var(--yellow-deep)"/>
      <polygon points="0,735 130,801 0,801" fill="var(--grey-band)" opacity=".7"/>
    </svg>
    <h2 class="eyebrow">OUR PRODUCT</h2>
    <div class="eyebrow-rule"></div>
    <h1 class="headline">DIESEL GENERATORS</h1>
    <h3 class="subhead">STANDBY<br>GENERATORS</h3>
    <div class="product-photo" role="img" aria-label="White enclosed 100 kW standby diesel generator with Brightline Energy name and brightlineenergyco.example"></div>
    <p class="features-label">FEATURES</p>
    <div class="features-panel">
      <ul class="feature-list">
        <li>30 to 500 KW powered by Fieldmark diesel engines. EPA Tier 2, Tier 3 and Tier i4</li>
        <li>13 to 60 KW powered by Kestrel diesel engines. EPA Tier i4</li>
        <li>Lerant Voss alternators • Stanwick (Corvan Generator Technologies) alternators [optional]</li>
        <li>Tidewell TWC 7000 series controllers for stand-alone operation • Tidewell TWC 8000 series controllers for paralleling operation [optional]</li>
        <li>12-Gauge steel enclosures with stainless steel hardware</li>
        <li>12-Gauge 5052 aluminum enclosures with stainless steel hardware [optional]</li>
        <li>Quietek Hood QX critical grade silencers</li>
        <li>Delvar manual main line circuit breakers</li>
        <li>Arcbridge manual and motorized main line circuit breakers [optional]</li>
        <li>50 to 5000-Gal, single-wall fuel tanks</li>
        <li>50 to 5000-Gal, double-walled UL142 listed fuel tanks</li>
        <li>Battery disconnect switch</li>
        <li>12V starting battery</li>
      </ul>
    </div>
    <div class="site-photo upper" style="left:418px" role="img" aria-label="Refinery pipework under orange light"></div>
    <div class="site-photo lower" style="left:418px" role="img" aria-label="Industrial machinery with orange equipment"></div>
    <div class="page-number"><span>06</span></div>
  </section>

  <section class="page page-right">
    <div class="page-backdrop" role="img" aria-label="Dark blue industrial interior with gas cylinders"></div>
    <svg class="bands" viewBox="0 0 600 801" aria-hidden="true">
      <polygon points="600,70 600,300 170,300 150,300" fill="var(--yellow)" opacity=".9"/>
      <polygon points="150,300 600,300 600,460 0,690" fill="var(--yellow)" opacity=".55"/>
      <polygon points="0,690 180,560 140,801 0,801" fill="var(--yellow)" opacity=".6"/>
      <polygon points="380,690 600,770 600,801 520,801 380,720" fill="var(--yellow-deep)"/>
      <polygon points="40,801 220,690 600,690 600,740 260,740 110,801" fill="var(--grey-band)"/>
      <polygon points="600,0 600,70 520,0" fill="var(--navy-deep)"/>
    </svg>
    <h2 class="eyebrow">OUR PRODUCT</h2>
    <div class="eyebrow-rule"></div>
    <h1 class="headline">DIESEL GENERATORS</h1>
    <h3 class="subhead">PRIME<br>GENERATORS</h3>
    <div class="product-photo" style="left:237px" role="img" aria-label="White enclosed 100 kW prime diesel generator with Brightline Energy name and brightlineenergyco.example"></div>
    <p class="features-label">FEATURES</p>
    <div class="features-panel" style="left:38px;width:357px">
      <ul class="feature-list" style="left:8px">
        <li>30 to 500 KW powered by Fieldmark diesel engines. EPA Tier 2, Tier 3 and Tier i4</li>
        <li>13 to 60 KW powered by Kestrel diesel engines. EPA Tier i4</li>
        <li>Lerant Voss alternators • Stanwick (Corvan Generator Technologies) alternators [optional]</li>
        <li>Tidewell TWC 7000 series controllers for stand-alone operation • Tidewell TWC 8000 series controllers for paralleling operation [optional]</li>
        <li>12-Gauge steel enclosures with stainless steel hardware</li>
        <li>12-Gauge 5052 aluminum enclosures with stainless steel hardware [optional]</li>
        <li>Quietek Hood QX critical grade silencers</li>
        <li>Delvar manual main line circuit breakers</li>
        <li>Arcbridge manual and motorized main line circuit breakers [optional]</li>
        <li>50 to 5000-Gal, single-wall fuel tanks</li>
        <li>50 to 5000-Gal, double-walled UL142 listed fuel tanks</li>
        <li>Battery disconnect switch</li>
        <li>12V starting battery</li>
      </ul>
    </div>
    <div class="site-photo upper" style="left:415px;top:502px;height:134px" role="img" aria-label="Refinery pipework under orange light"></div>
    <div class="site-photo lower" style="left:415px;top:642px;height:140px" role="img" aria-label="Industrial machinery with orange equipment"></div>
    <div class="page-number" style="left:10px"><span>07</span></div>
  </section>

</main>
</body>
</html>
```